Create a memorable Web Design for real estate branding

we are a Minnepolis brokerage and boutique housing specialist with over 27 years of experience in the Global furnished housing industry, servicing the Greater Los Angeles area. Specializing in “warm environments” we offer a customized approach to satisfying our guests and client’s needs by offering a wide array of options in highly desirable areas. Additionally, Lantern Dwelling Partners offers assistance and expertise to home buyers, sellers and investors.

Industry/Entity Type

Real Estate

Number of Pages Required

1 page

Font styles to use
Serif
Sans Serif
Decorative

```html
<!DOCTYPE html>
<html lang="en">
<head>
<meta charset="utf-8">
<title>Marlo Kestrel Real Estate</title>
<link href="https://fonts.googleapis.com/css2?family=Open+Sans:wght@400;600;700&display=swap" rel="stylesheet">
<style>
:root{
  --green:#1f9c7f;
  --green-dark:#157a63;
  --green-light:#2cb394;
  --price:#27a24f;
  --text:#333;
  --muted:#555;
  --panel:#ececec;
  --dark:#2c2f31;
  --footer:#2f3133;
  --white:#fff;
}
*{box-sizing:border-box;margin:0;padding:0}
html,body{width:1200px;height:2253px;overflow:hidden;background:var(--white);font-family:"Open Sans",Arial,sans-serif;color:var(--text)}
.page{position:relative;width:1200px;height:2253px;overflow:hidden}

.header{position:absolute;left:0;top:0;width:1200px;height:90px;border-top:3px solid var(--green);background:var(--white)}
.brand{position:absolute;left:98px;top:16px;color:var(--green);font-weight:600;line-height:1}
.brand .name{font-size:32px;display:block}
.brand .sub{font-size:18px;display:block;margin-left:78px;margin-top:4px;letter-spacing:1px}
.search{position:absolute;left:800px;top:28px;width:301px;height:37px;border:1px solid #d6d6d6;display:flex}
.search span{flex:1;font-size:10px;color:#999;padding:11px 12px}
.search .btn{width:49px;background:var(--green);display:flex;align-items:center;justify-content:center}

.nav{position:absolute;left:0;top:90px;width:1200px;height:48px;background:linear-gradient(var(--green-light),var(--green-dark));color:var(--white);font-size:12px;font-weight:600;text-transform:uppercase}
.nav a{position:absolute;top:16px;color:var(--white);text-decoration:none;display:flex;align-items:center;gap:8px}
.flag{position:absolute;left:1048px;top:12px;width:53px;height:24px;display:flex}
.flag i{display:block;height:100%}

.hero{position:absolute;left:0;top:138px;width:1200px;height:520px}
.hero-photo{position:absolute;inset:0;background:linear-gradient(180deg,#3b3f43 0%,#5a5c55 35%,#3e4a32 70%,#2d3526 100%);clip-path:polygon(0 0,100% 0,100% 92%,50% 100%,0 92%)}
.hero-title{position:absolute;left:0;width:1200px;top:160px;text-align:center;color:var(--white);font-size:64px;font-weight:700;letter-spacing:1px}
.hero-sub{position:absolute;left:0;width:1200px;top:248px;text-align:center;color:var(--white);font-size:34px;font-weight:400}
.hero-cta{position:absolute;left:484px;top:320px;width:230px;height:38px;border:1px solid var(--white);color:var(--white);font-size:18px;text-align:center;line-height:36px}
.arrow{position:absolute;top:194px}

.about{position:absolute;left:99px;top:658px;width:1002px;height:435px;background:var(--panel);box-shadow:0 0 4px rgba(0,0,0,.15)}
.about-band{position:absolute;left:0;top:0;width:1002px;height:105px}
.about-title{position:absolute;left:0;top:60px;width:1002px;text-align:center;color:var(--white);font-size:21px;font-weight:600}
.about-photo{position:absolute;left:48px;top:162px;width:337px;height:216px;border:4px solid var(--white);box-shadow:0 0 3px rgba(0,0,0,.3);background:linear-gradient(135deg,#5d6b7a,#c9d6dd 60%,#b97b54)}
.about-body{position:absolute;left:428px;top:153px;width:540px;display:flex;flex-direction:column;align-items:flex-start}
.about-text{font-size:12px;line-height:28px;color:var(--text);text-align:justify;hyphens:auto;-webkit-hyphens:auto}
.outline-btn{display:block;border:1px solid var(--green);color:var(--green);font-size:16px;font-weight:600;text-align:center;background:var(--white);width:117px;height:36px;line-height:34px;margin-top:14px}

.featured{position:absolute;left:0;top:1137px;width:1200px;height:593px;background:linear-gradient(135deg,#3a3d40,#25282a 60%,#34373a)}
.section-title{position:absolute;left:0;width:1200px;text-align:center;font-weight:600}
.card{position:absolute;top:129px;width:321px;height:389px;background:var(--white);text-align:center}
.card .photo{position:absolute;left:6px;top:8px;width:309px;height:196px}
.card .buy{position:absolute;left:106px;top:188px;width:110px;height:40px;background:linear-gradient(var(--green-light),var(--green-dark));color:var(--white);font-size:17px;line-height:40px;font-weight:600}
.card h3{position:absolute;left:0;width:100%;top:248px;font-size:18px;font-weight:600;color:var(--text)}
.card .price{position:absolute;left:0;width:100%;top:284px;font-size:21px;color:var(--price)}
.card p{position:absolute;left:30px;width:261px;top:318px;font-size:12.5px;line-height:21px;color:var(--muted)}

.gallery-card{position:absolute;top:1849px;width:246px;height:242px;background:var(--white);border:1px solid #ddd;box-shadow:0 1px 4px rgba(0,0,0,.2);text-align:center}
.gallery-card .photo{position:absolute;left:4px;top:3px;width:236px;height:186px}
.gallery-card .pin{position:absolute;left:112px;top:7px;width:20px;height:20px;border-radius:50%;background:#e02020}
.gallery-card span{position:absolute;left:0;width:100%;top:206px;font-size:16px;font-weight:600;color:var(--text)}

.footer{position:absolute;left:0;top:2145px;width:1200px;height:108px;background:var(--footer);color:var(--white)}
.footer .brand{left:99px;top:14px;color:var(--white)}
.footer .brand .name{font-size:40px}
.footer .brand .sub{font-size:22px;margin-left:140px;margin-top:2px}
.footer .divider{position:absolute;left:505px;top:12px;width:1px;height:84px;background:#555}
.footer-links a{position:absolute;top:29px;color:var(--white);font-size:12px;font-weight:600;text-decoration:none}
.footer-links i{position:absolute;top:32px;width:4px;height:4px;border-radius:50%;background:var(--white)}
.copyright{position:absolute;left:505px;width:695px;top:64px;text-align:center;font-size:12px;color:#ddd}
</style>
</head>
<body>
<div class="page">

  <header class="header">
    <div class="brand"><span class="name">Marlo Kestrel</span><span class="sub">REAL ESTATE</span></div>
    <div class="search"><span>Search Here</span><div class="btn">
      <svg width="20" height="20" viewBox="0 0 20 20"><circle cx="8" cy="8" r="5.5" fill="none" stroke="#fff" stroke-width="2.5"/><line x1="12" y1="12" x2="18" y2="18" stroke="#fff" stroke-width="3" stroke-linecap="round"/></svg>
    </div></div>
  </header>

  <nav class="nav">
    <a style="left:100px">Home</a>
    <a style="left:240px">Features</a>
    <a style="left:400px">Gallery</a>
    <a style="left:553px">Contact Me</a>
    <a style="left:725px;top:13px"><svg width="18" height="18" viewBox="0 0 18 18"><rect x="7" y="2" width="9" height="14" fill="none" stroke="#fff" stroke-width="2"/><path d="M1 9h9M7 6l3 3-3 3" fill="none" stroke="#fff" stroke-width="2"/></svg>Login</a>
    <a style="left:879px;top:13px"><svg width="18" height="18" viewBox="0 0 18 18"><circle cx="9" cy="9" r="8.5" fill="#fff"/><circle cx="9" cy="7" r="3" fill="#1f9c7f"/><path d="M3.5 14.5c1.5-3 9.5-3 11 0" fill="#1f9c7f"/></svg>My Account</a>
    <div class="flag"><i style="width:21px;background:#0a7a2e"></i><i style="width:32px;background:#e0201e"></i></div>
  </nav>

  <section class="hero">
    <div class="hero-photo" role="img" aria-label="Photo of a two-storey suburban house with landscaped garden and a for-sale sign at dusk"></div>
    <svg class="arrow" style="left:50px" width="16" height="24" viewBox="0 0 16 24"><path d="M12 3 4 12l8 9" fill="none" stroke="#fff" stroke-width="3"/></svg>
    <svg class="arrow" style="left:1134px" width="16" height="24" viewBox="0 0 16 24"><path d="M4 3l8 9-8 9" fill="none" stroke="#fff" stroke-width="3"/></svg>
    <h1 class="hero-title">Marlo Kestrel</h1>
    <p class="hero-sub">Specializing in “warm environments”</p>
    <div class="hero-cta">Get In Touch With us</div>
  </section>

  <section class="about">
    <svg class="about-band" viewBox="0 0 1002 105" preserveAspectRatio="none">
      <defs><linearGradient id="band" x1="0" y1="0" x2="0" y2="1"><stop offset="0" stop-color="#2cb394"/><stop offset="1" stop-color="#157a63"/></linearGradient></defs>
      <path d="M0 0 L501 22 L1002 0 V105 H0 Z" fill="url(#band)"/>
      <circle cx="481" cy="24" r="5" fill="#7fd03a"/><circle cx="501" cy="24" r="5" fill="#0d5a48"/><circle cx="521" cy="24" r="5" fill="#7fd03a"/>
    </svg>
    <h2 class="about-title">About MARLO KESTREL</h2>
    <div class="about-photo" role="img" aria-label="Photo of a small model house on a desk with people signing documents"></div>
    <div class="about-body">
      <p class="about-text">Mea in quis meliore. Duo ei ponderum adversarium. Vim te dolorum appetere, ne stet repudiare vis. Ei solum ludus liberavisse ius. Vim an dicta sapientem honestatis, pro ne purto adipiscing. Mei cu summo impedit, no scaevola patrioque est, sea persius sensibus eleifend ea . Mea in quis meliore. Duo ei ponderum adversarium. Vim te dolorum appetere, ne stet repudiare vis. Ei solum ludus liberavisse ius. Vim an dicta sapientem honestatis, pro ne purto adipiscing. Mei cu summo impedit, no scaevola patrioque est, sea persius sensibus eleifend ea.</p>
      <div class="outline-btn">More Info</div>
    </div>
  </section>

  <section class="featured" role="region" aria-label="Featured projects">
    <h2 class="section-title" style="top:48px;font-size:21px;color:#fff">Our Featured Projects</h2>
    <div class="card" style="left:99px">
      <div class="photo" role="img" aria-label="Photo of a woman with a laptop outside a house" style="background:linear-gradient(160deg,#dfe9e6,#8ea970 55%,#4e6b37)"></div>
      <div class="buy">Buy Now</div>
      <h3>Pertinacia reprehendunt cu</h3>
      <div class="price">$ 769.00</div>
      <p>Ut mel quot vidisse maiestatis, ex vivendo abhorreant duo. Dicat saepe incideri mea ex</p>
    </div>
    <div class="card" style="left:439px">
      <div class="photo" role="img" aria-label="Photo of a modern home entrance with open glass door and patio" style="background:linear-gradient(120deg,#5a3a28,#a26a3e 45%,#3d5a35)"></div>
      <div class="buy">Buy Now</div>
      <h3>Maiorum blandit et</h3>
      <div class="price">$ 365.00</div>
      <p>Ut mel quot vidisse maiestatis, ex vivendo abhorreant duo. Dicat saepe incideri mea ex</p>
    </div>
    <div class="card" style="left:780px">
      <div class="photo" role="img" aria-label="Photo of a couple talking with an agent holding a tablet" style="background:linear-gradient(120deg,#8fc2c9,#d7c2ad 55%,#6d5140)"></div>
      <div class="buy">Buy Now</div>
      <h3>Prima voluptatum ex</h3>
      <div class="price">$ 654.00</div>
      <p>Ut mel quot vidisse maiestatis, ex vivendo abhorreant duo. Dicat saepe incideri mea ex</p>
    </div>
  </section>

  <h2 class="section-title" style="top:1773px;font-size:23px;color:var(--green)">Our Photo Gallery</h2>
  <div class="gallery-card" style="left:99px">
    <div class="photo" role="img" aria-label="Photo of a large two-storey family house" style="background:linear-gradient(180deg,#6f9fd6,#c8ab84 55%,#4f6b33)"></div>
    <i class="pin"></i><span>Scaevola Patrioque</span>
  </div>
  <div class="gallery-card" style="left:351px">
    <div class="photo" role="img" aria-label="Photo of a modern white house with palm trees" style="background:linear-gradient(180deg,#e6ecef,#c9c5bd 55%,#4d6b3a)"></div>
    <i class="pin"></i><span>Consul debitis invenire</span>
  </div>
  <div class="gallery-card" style="left:604px">
    <div class="photo" role="img" aria-label="Photo of a house with wooden deck and patio furniture" style="background:linear-gradient(180deg,#3d5a3a,#8b6a4c 55%,#7a4a2c)"></div>
    <i class="pin"></i><span>Scaevola Patrioque</span>
  </div>
  <div class="gallery-card" style="left:856px">
    <div class="photo" role="img" aria-label="Photo of a family running on the lawn in front of a house" style="background:linear-gradient(180deg,#b9d5e8,#a58a70 50%,#6d9a3e)"></div>
    <i class="pin"></i><span>Consul debitis invenire</span>
  </div>

  <footer class="footer">
    <div class="brand"><span class="name">Marlo Kestrel</span><span class="sub">REAL ESTATE</span></div>
    <div class="divider"></div>
    <div class="footer-links">
      <a style="left:571px">HOME</a><i style="left:655px"></i>
      <a style="left:710px">FEATURES</a><i style="left:820px"></i>
      <a style="left:871px">GALLERY</a><i style="left:972px"></i>
      <a style="left:1026px">CONTACT ME</a>
    </div>
    <p class="copyright">All Rights Reseved . copyrights2016@companyname.com</p>
  </footer>

</div>
</body>
</html>
```